Software Development Consulting Company Needs Business Card Design

We need a new business card design for our consultants at Kestrel Works (kestrelworks.example). We are a small firm that provides high-end software development and methodology consulting to medium to large enterprise IT organizations.

Our logo uses Futura for the font and we would like to stick with navy blue and canary yellow for the logo colors. Attached are normal and reversed versions of our logos in illustrator format.
Updates

Hi Everyone, Thank yo very much for your amazing design ideas. I have created a poll for this project and our employees will be voting on the design they wish to use. We will be making a decision this Wednesday (October 22nd). Thanks again, Dale Hartwick

Industry/Entity Type

Business

```html
<!DOCTYPE html>
<html lang="en">
<head>
<meta charset="utf-8">
<title>Kestrel Works – Business Card</title>
<link rel="stylesheet" href="https://fonts.googleapis.com/css2?family=Jost:wght@500&family=Open+Sans:wght@400;600;700&display=swap">
<style>
  :root {
    --navy: #1b4a72;
    --canary: #f3e61b;
    --ink: #4a4f55;
    --muted: #6b6f74;
    --card: #ffffff;
    --backdrop: #e9e7e3;
  }
  * { box-sizing: border-box; margin: 0; padding: 0; }
  html, body { width: 1200px; height: 720px; overflow: hidden; }
  body {
    background: var(--backdrop);
    font-family: "Open Sans", Arial, sans-serif;
    position: relative;
  }
  .card {
    position: absolute;
    top: 211px;
    width: 520px;
    height: 297px;
    background: var(--card);
    box-shadow: 0 6px 18px rgba(0,0,0,.18);
    overflow: hidden;
  }
  .card--front { left: 50px; }
  .card--back { left: 630px; }
  .card__wave { position: absolute; inset: 0; }

  .brand {
    position: absolute;
    display: flex;
    align-items: center;
    gap: 12px;
  }
  .brand__dot {
    width: 14px; height: 14px;
    border-radius: 50%;
    background: var(--canary);
    flex: none;
  }
  .brand__name {
    font-family: "Jost", "Futura", sans-serif;
    font-weight: 500;
    color: var(--navy);
    letter-spacing: 0.12em;
    white-space: nowrap;
  }
  .card--front .brand { left: 72px; top: 38px; }
  .card--front .brand__name { font-size: 30px; }
  .card--back .brand { left: 50%; top: 92px; transform: translateX(-50%); }
  .card--back .brand__name { font-size: 36px; }

  .contact {
    position: absolute;
    font-size: 11.5px;
    color: var(--ink);
    line-height: 1;
    white-space: nowrap;
  }
  .contact__line { display: flex; align-items: center; gap: 6px; height: 20px; }
  .contact__icon { width: 12px; height: 12px; flex: none; }
  .contact--place { left: 72px; top: 120px; }
  .contact--reach { left: 258px; top: 100px; }
  .contact__divider {
    position: absolute;
    left: 244px; top: 100px;
    width: 1px; height: 44px;
    background: #c9c9c9;
  }

  .holder {
    position: absolute;
    right: 42px; bottom: 26px;
    color: #ffffff;
    font-size: 15px;
    font-weight: 700;
  }
  .holder__title { font-weight: 400; font-size: 12px; }

  .web-address {
    position: absolute;
    left: 0; right: 0; bottom: 58px;
    text-align: center;
    font-size: 17px;
    letter-spacing: 0.16em;
    color: var(--muted);
  }
</style>
</head>
<body>

<section class="card card--front" aria-label="Card front">
  <svg class="card__wave" viewBox="0 0 520 297" aria-hidden="true">
    <path d="M0 262 C150 278 290 250 380 205 C440 175 480 160 520 152 L520 297 L0 297 Z" fill="var(--navy)"/>
    <path d="M0 250 C150 266 290 238 380 193 C440 163 480 148 520 140" fill="none" stroke="var(--canary)" stroke-width="5"/>
  </svg>

  <div class="brand">
    <span class="brand__dot"></span>
    <span class="brand__name">KESTREL WORKS</span>
  </div>

  <div class="contact contact--place">
    <div class="contact__line">Northfield + Ashby, IL</div>
    <div class="contact__line">
      <svg class="contact__icon" viewBox="0 0 12 12" aria-hidden="true">
        <circle cx="6" cy="6" r="5.5" fill="var(--muted)"/>
        <path d="M0.8 6H11.2M6 0.8V11.2M6 0.8C3.5 3.5 3.5 8.5 6 11.2M6 0.8C8.5 3.5 8.5 8.5 6 11.2" stroke="#fff" stroke-width="0.7" fill="none"/>
      </svg>
      www.kestrelworks.example
    </div>
  </div>

  <span class="contact__divider"></span>

  <div class="contact contact--reach">
    <div class="contact__line">
      <svg class="contact__icon" viewBox="0 0 12 12" aria-hidden="true">
        <circle cx="6" cy="6" r="5.5" fill="none" stroke="var(--muted)" stroke-width="1"/>
        <path d="M4 3.2 L5 3 L5.6 4.6 L4.9 5.2 C5.3 6 6 6.7 6.8 7.1 L7.4 6.4 L9 7 L8.8 8 C6.3 8.3 3.7 5.7 4 3.2Z" fill="var(--muted)"/>
      </svg>
      012-555-0147
    </div>
    <div class="contact__line">
      <svg class="contact__icon" viewBox="0 0 12 12" aria-hidden="true">
        <rect x="0.5" y="2.5" width="11" height="7.5" rx="1" fill="var(--muted)"/>
        <path d="M1 3 L6 7 L11 3" stroke="#fff" stroke-width="0.9" fill="none"/>
      </svg>
      info@kestrelworks.example
    </div>
  </div>

  <p class="holder">Your Name, <span class="holder__title">Title</span></p>
</section>

<section class="card card--back" aria-label="Card back">
  <div class="brand">
    <span class="brand__dot"></span>
    <span class="brand__name">KESTREL WORKS</span>
  </div>
  <p class="web-address">www.kestrelworks.example</p>
</section>

</body>
</html>
```